KAJU Freightways #ALLKAJU Business Cards & Letterhead

I am looking to business cards designed for our organization. We are currently undergoing a small re-branding that is taking place. Our organization is called KAJU Freightways and we are headquartered in Phoenix, AZ. We primarily provide transportation and logistics services to the Marlow Parcel Bureau who is our largest customer. I would like to see a design that incorporates name, title, contact info, website, and address (this will be different depending on the employee). I would also like to see some color on the business card using our logo colors or a variation. I would like our logo on the back of the business card with the website displayed. The final design should communicate that we are a next generation transportation operate that focuses on being driver-first, customer-centric, innovative, and sustainable.We would also like our #ALLKAJU catch phrase incorporated as well.

Target Market(s)

Transportation & Logistics

Industry/Entity Type

Trucking Company

Contact Information for Business Card

-First and Last Name
-Position Title
-Contact Phone
-Contact Email
-Physical Address

Font styles to use
Serif

Colors

Designer to choose colors to be used in the design.

Requirements
Must have
• -KAJU logo prominently displayed
• -#ALLKAJU catch phrase used
• -Some amount of color, design gradient, etc.
• -Logo on the back with website listed (https://www.kajufreightco.example)

```html
<!DOCTYPE html>
<html lang="en">
<head>
<meta charset="utf-8">
<title>KAJU Freightways Business Card</title>
<link href="https://fonts.googleapis.com/css2?family=Roboto+Slab:wght@400;500;700;900&display=swap" rel="stylesheet">
<style>
  :root {
    --backdrop: #3b3b3b;
    --card: #1d1d1e;
    --ink: #f2f2f2;
    --silver: #9a9a9a;
    --green: #7dc42a;
    --teal: #1f5f66;
  }
  * { margin: 0; padding: 0; box-sizing: border-box; }
  html, body { width: 799px; height: 1200px; overflow: hidden; }
  body {
    background: var(--backdrop);
    font-family: "Roboto Slab", Georgia, serif;
    color: var(--ink);
    position: relative;
  }
  .card {
    position: absolute;
    left: 50px;
    width: 699px;
    height: 400px;
    background: var(--card);
    border-radius: 4px;
    box-shadow: 0 14px 30px rgba(0,0,0,.45);
  }
  .card--front { top: 110px; }
  .card--back { top: 660px; }

  .mark-dot {
    width: 22px; height: 22px; border-radius: 50%;
    border: 3px solid currentColor;
    flex: none;
  }

  /* Front */
  .front-mark {
    position: absolute;
    left: 0; right: 0; top: 120px;
    display: flex; align-items: center; justify-content: center; gap: 16px;
    color: var(--silver);
  }
  .front-mark .wordmark {
    font-size: 74px; font-weight: 900; letter-spacing: 2px; line-height: 1;
  }
  .front-web {
    position: absolute; left: 0; right: 0; top: 298px;
    display: flex; align-items: center; justify-content: center; gap: 22px;
    font-size: 16px; letter-spacing: 3px; color: var(--ink);
  }
  .front-web .dash { width: 38px; height: 3px; background: var(--green); flex: none; }

  /* Back */
  .back-mark {
    position: absolute; left: 46px; top: 42px;
    display: flex; align-items: center; gap: 12px;
  }
  .back-mark .mark-dot { color: var(--green); width: 26px; height: 26px; border-width: 4px; }
  .back-mark .wordmark { font-size: 54px; font-weight: 900; color: var(--ink); line-height: 1; }
  .person { position: absolute; right: 50px; top: 102px; text-align: right; }
  .person .name { font-size: 28px; font-weight: 700; line-height: 1.2; }
  .person .title { font-size: 17px; margin-top: 2px; }
  .divider {
    position: absolute; left: 46px; right: 46px; top: 174px; height: 2px;
    background: linear-gradient(90deg, var(--teal), var(--green));
  }
  .contacts { position: absolute; left: 46px; top: 210px; width: 320px; list-style: none; }
  .contacts li {
    display: flex; align-items: center; gap: 12px;
    font-size: 16px; line-height: 28px; white-space: nowrap;
  }
  .contacts svg { width: 15px; height: 15px; fill: var(--green); flex: none; }
  .company { position: absolute; right: 50px; top: 210px; width: 300px; text-align: right; }
  .company .company-name { font-size: 17px; font-weight: 700; color: var(--green); margin-bottom: 6px; white-space: nowrap; }
  .company address { font-style: normal; font-size: 17px; line-height: 26px; }
  .tagline {
    position: absolute; right: 50px; bottom: 34px;
    font-size: 16px; font-weight: 700; letter-spacing: 3px; color: var(--green);
  }
</style>
</head>
<body>
  <section class="card card--front" aria-label="Card front">
    <div class="front-mark">
      <span class="mark-dot"></span>
      <span class="wordmark">KAJU</span>
    </div>
    <div class="front-web">
      <span class="dash"></span>
      <span>www.kajufreightco.example</span>
      <span class="dash"></span>
    </div>
  </section>

  <section class="card card--back" aria-label="Card back">
    <div class="back-mark">
      <span class="wordmark">KAJU</span>
      <span class="mark-dot"></span>
    </div>
    <div class="person">
      <p class="name">Daniel Okafor</p>
      <p class="title">Chairman &amp; CEO</p>
    </div>
    <div class="divider"></div>
    <ul class="contacts">
      <li>
        <svg viewBox="0 0 24 24"><path d="M6.6 10.8a15.1 15.1 0 0 0 6.6 6.6l2.2-2.2a1 1 0 0 1 1-.25 11.4 11.4 0 0 0 3.6.57 1 1 0 0 1 1 1V20a1 1 0 0 1-1 1A17 17 0 0 1 3 4a1 1 0 0 1 1-1h3.5a1 1 0 0 1 1 1c0 1.25.2 2.45.57 3.57a1 1 0 0 1-.25 1z"/></svg>
        555-014-2290
      </li>
      <li>
        <svg viewBox="0 0 24 24"><path d="M2 5h20v14H2zm2 2v.5l8 5 8-5V7l-8 5z"/></svg>
        daniel@kajufreightco.example
      </li>
      <li>
        <svg viewBox="0 0 24 24"><path d="M12 2a10 10 0 1 0 0 20 10 10 0 0 0 0-20zm6.9 9h-3a15 15 0 0 0-1.3-5.6A8 8 0 0 1 18.9 11zM12 4.1c.9 1.2 1.8 3.5 1.9 6.9h-3.8c.1-3.4 1-5.7 1.9-6.9zM9.4 5.4A15 15 0 0 0 8.1 11h-3a8 8 0 0 1 4.3-5.6zM5.1 13h3a15 15 0 0 0 1.3 5.6A8 8 0 0 1 5.1 13zm6.9 6.9c-.9-1.2-1.8-3.5-1.9-6.9h3.8c-.1 3.4-1 5.7-1.9 6.9zm2.6-1.3a15 15 0 0 0 1.3-5.6h3a8 8 0 0 1-4.3 5.6z"/></svg>
        www.kajufreightco.example
      </li>
    </ul>
    <div class="company">
      <p class="company-name">KAJU Freightways &amp; Energy</p>
      <address>1450 North Saguaro Ridge<br>Road Mesa, AZ 85201</address>
    </div>
    <p class="tagline">#ALLKAJU</p>
  </section>
</body>
</html>
```